Business Card Design

My business is writing crime novels to entertain readers. I write legal thrillers and mysteries. I need a card for publishers, agents, other authors, and media.

Industry/Entity Type

Legal

Contact Information for Business Card

Paul Derrow
www.derrowfiction.example
pauljderrow@inkpost.example
0064 27 5190472

```html
<!DOCTYPE html>
<html lang="en">
<head>
<meta charset="utf-8">
<title>Paul Derrow — Business Card</title>
<link rel="stylesheet" href="https://fonts.googleapis.com/css2?family=Libre+Baskerville:wght@700&family=Open+Sans:wght@400&display=swap">
<style>
  :root {
    --page-bg: #e9e7e3;
    --card-bg: #ffffff;
    --name-ink: #4f545c;
    --text-ink: #2f3236;
    --icon-ink: #3a3d42;
    --rule: #8a8c90;
    --photo-frame: #1e1f21;
    --photo-light: #b9b9b9;
    --photo-dark: #6f6f6f;
  }
  html, body {
    margin: 0;
    padding: 0;
    width: 1200px;
    height: 800px;
    overflow: hidden;
    background: var(--page-bg);
  }
  .canvas {
    position: relative;
    width: 1200px;
    height: 800px;
  }
  .card {
    position: absolute;
    left: 150px;
    top: 150px;
    width: 900px;
    height: 500px;
    background: var(--card-bg);
    box-shadow: 0 6px 24px rgba(0, 0, 0, 0.12);
  }
  .portrait {
    position: absolute;
    left: 110px;
    top: 130px;
    width: 270px;
    height: 250px;
    box-sizing: border-box;
    border: 2px solid var(--photo-frame);
    background: linear-gradient(160deg, var(--photo-light) 0%, #9a9a9a 55%, var(--photo-dark) 100%);
  }
  .divider {
    position: absolute;
    left: 440px;
    top: 120px;
    width: 2px;
    height: 270px;
    background: var(--rule);
  }
  .name {
    position: absolute;
    left: 500px;
    top: 92px;
    margin: 0;
    font-family: "Libre Baskerville", Georgia, serif;
    font-weight: 700;
    font-size: 27px;
    letter-spacing: 0.5px;
    text-transform: uppercase;
    color: var(--name-ink);
  }
  .contact-list {
    position: absolute;
    left: 500px;
    top: 252px;
    margin: 0;
    padding: 0;
    list-style: none;
  }
  .contact-item {
    display: flex;
    align-items: center;
    height: 40px;
    font-family: "Open Sans", Arial, sans-serif;
    font-size: 20px;
    letter-spacing: 1.2px;
    color: var(--text-ink);
  }
  .contact-icon {
    width: 26px;
    height: 20px;
    margin-right: 16px;
    flex: none;
  }
</style>
</head>
<body>
<main class="canvas">
  <section class="card">
    <div class="portrait" role="img" aria-label="Portrait photograph of the author"></div>
    <div class="divider"></div>
    <h1 class="name">Paul Derrow</h1>
    <ul class="contact-list">
      <li class="contact-item">
        <svg class="contact-icon" viewBox="0 0 26 20" aria-hidden="true">
          <rect x="7" y="2" width="12" height="16" rx="1.5" fill="none" stroke="var(--icon-ink)" stroke-width="2"/>
        </svg>
        0064 27 5190472
      </li>
      <li class="contact-item">
        <svg class="contact-icon" viewBox="0 0 26 20" aria-hidden="true">
          <rect x="3" y="2" width="20" height="12" rx="1" fill="none" stroke="var(--icon-ink)" stroke-width="2"/>
          <rect x="9" y="16" width="8" height="2" fill="var(--icon-ink)"/>
        </svg>
        www.derrowfiction.example
      </li>
      <li class="contact-item">
        <svg class="contact-icon" viewBox="0 0 26 20" aria-hidden="true">
          <rect x="3" y="3" width="20" height="14" fill="var(--icon-ink)"/>
          <path d="M3 3 L13 11 L23 3" fill="none" stroke="#ffffff" stroke-width="1.5"/>
        </svg>
        pauljderrow@inkpost.example
      </li>
    </ul>
  </section>
</main>
</body>
</html>
```